Sophisticated, clean website reflecting my feminine, playful side to sell my abstract art,

I need a website no more than 3 pages to showcase my paintings, a little about me and some contact info. I do abstracts so looking for something a little edgy, yet feminine and current.
Updates

Hi there, These are some artists websites that I Iike: Marnelvoss.com (I like how airy it is) peterwallombry.com garethpolvens.com (I like how it scrolls) I'll need a place for a photo ( a headshot-i do not have it yet so I'll need to be able to upload that later) as well as an area for my bio. Also, it's important that I will be able to upload any new photos and descriptions easily so it should be user friendly. Lastly, I like in a sunny place so would like to have this seem upbeat and playful as that is how i like to paint. thanks-I'm trying to upload my photos now -

Target Market(s)

ppl ages 35-70 who want large scale art for their homes

Industry/Entity Type

art

Coding

Coded - Design and coding required

Number of Pages Required

3 page

Colors

Designer to choose colors to be used in the design.

Requirements
Must have
• photos of my art, a place for my bio, be easy to reach me. tasteful-nothing too "in your face" -my clients are pretty high end and organized. They like clean lines
Nice to have
• sophisticated background, muted tones in the back-similar clean font throughout-no cursive
Should not have
• too many dark areas. Too many blocks of color. Too serious.

```html
<!DOCTYPE html>
<html lang="en">
<head>
<meta charset="utf-8">
<title>Lena Marlowe Abstracts — Gallery</title>
<link rel="stylesheet" href="https://fonts.googleapis.com/css2?family=Oswald:wght@300;400&family=Mada:wght@400&display=swap">
<style>
  :root {
    --ink: #1a1a1a;
    --paper: #ffffff;
    --sun: #f1d35e;
    --rule: #6e6e6e;
    --veil: rgba(255,255,255,0.86);
  }
  * { box-sizing: border-box; margin: 0; padding: 0; }
  html, body { width: 994px; height: 1200px; overflow: hidden; background: var(--paper); }
  body { position: relative; color: var(--ink); font-family: "Oswald", sans-serif; }

  .brand { position: absolute; left: 0; width: 994px; top: 0; text-align: center; }
  .brand__name {
    position: absolute; left: 0; width: 994px; top: 44px;
    font-weight: 400; font-size: 34px; letter-spacing: 3px; line-height: 1;
  }
  .brand__rule {
    position: absolute; left: 426px; top: 121px; width: 142px; height: 1px; background: var(--rule);
  }
  .brand__tagline {
    position: absolute; left: 0; width: 994px; top: 126px;
    font-weight: 300; font-size: 11.5px; letter-spacing: 0.2px;
  }

  .site-nav {
    position: absolute; left: 0; width: 994px; top: 150px;
    display: flex; justify-content: center; gap: 31px;
    font-weight: 400; font-size: 14.5px;
  }
  .site-nav a { color: var(--ink); text-decoration: none; }
  .site-nav a.is-current { color: var(--sun); }

  .artwork { position: absolute; width: 238px; }
  .artwork__image { width: 238px; height: 317px; position: relative; overflow: hidden; }
  .artwork__title {
    margin-top: 15px; text-align: center; font-weight: 400; font-size: 12.5px;
  }
  .artwork--1 { left: 224px; top: 200px; }
  .artwork--2 { left: 531px; top: 200px; }
  .artwork--3 { left: 224px; top: 582px; }
  .artwork--4 { left: 531px; top: 582px; }

  .paint--blush { background: radial-gradient(circle at 55% 50%, #efe0dc 0%, #d7a8b4 45%, #6a2f45 80%, #2b1b22 100%); }
  .paint--tide { background: linear-gradient(180deg, #d7cbbd 0%, #c9b8a3 45%, #8f7a62 58%, #3f88ad 64%, #6fb3cf 85%, #a9d2e0 100%); }
  .paint--burst { background: radial-gradient(circle at 50% 60%, #e8e5dc 0%, #2f6d5a 35%, #c1773a 65%, #3e9aa7 100%); }
  .paint--sunwheel { background: radial-gradient(circle at 50% 55%, #f2efe6 0%, #d9a524 35%, #b8451f 70%, #5d8fc4 100%); }

  .artwork__details {
    position: absolute; left: 14px; top: 19px; width: 210px; height: 281px;
    background: var(--veil);
  }
  .details__title {
    position: absolute; left: 18px; top: 40px;
    display: flex; align-items: center; gap: 9px;
    font-weight: 300; font-size: 14px;
  }
  .details__title::after { content: ""; width: 70px; height: 1px; background: var(--ink); }
  .details__row {
    position: absolute; left: 18px; display: flex; align-items: center; gap: 10px;
    font-family: "Mada", sans-serif; font-size: 9.5px;
  }
  .details__row--size { top: 91px; }
  .details__row--medium { top: 126px; }
  .details__pointer { position: absolute; right: 10px; bottom: 30px; }

  .site-footer {
    position: absolute; left: 0; width: 994px; top: 1178px; text-align: center;
    font-family: "Mada", sans-serif; font-size: 9px;
  }
</style>
</head>
<body>
  <header class="brand">
    <div class="brand__name">LENA MARLOWE</div>
    <div class="brand__rule"></div>
    <div class="brand__tagline">LENA MARLOWE ABSTRACTS</div>
  </header>

  <nav class="site-nav">
    <a href="#" class="is-current">Gallery</a>
    <a href="#">About</a>
    <a href="#">Contact</a>
  </nav>

  <main>
    <figure class="artwork artwork--1">
      <div class="artwork__image paint--blush" role="img" aria-label="Abstract painting in blush pink, cream and deep plum brushstrokes">
        <div class="artwork__details">
          <div class="details__title">Donec pede justo</div>
          <div class="details__row details__row--size">
            <svg width="18" height="18" viewBox="0 0 18 18" fill="none" stroke="#1a1a1a" stroke-width="0.9"><path d="M2 16 L16 2 M11 2 H16 V7 M2 11 V16 H7"/></svg>
            <span>13-1, 40" x 40</span>
          </div>
          <div class="details__row details__row--medium">
            <svg width="18" height="18" viewBox="0 0 18 18" fill="none" stroke="#1a1a1a" stroke-width="0.9"><rect x="1" y="1" width="16" height="16"/><path d="M15 1 V17"/></svg>
            <span>Mixed media on canvas</span>
          </div>
          <svg class="details__pointer" width="18" height="22" viewBox="0 0 18 22" fill="none" stroke="#1a1a1a" stroke-width="0.9" stroke-linejoin="round"><path d="M6 12 V2.5 a1.3 1.3 0 0 1 2.6 0 V10 V8 a1.3 1.3 0 0 1 2.6 0 V10.5 V9 a1.3 1.3 0 0 1 2.6 0 V11 a1.3 1.3 0 0 1 2.6 0 V15 c0 3.5 -2.5 6 -6 6 h-1 c-2.5 0 -4 -1.5 -5 -3.5 L1.5 13 a1.3 1.3 0 0 1 2.2 -1.3 Z"/></svg>
        </div>
      </div>
      <figcaption class="artwork__title">Donec pede justo</figcaption>
    </figure>

    <figure class="artwork artwork--2">
      <div class="artwork__image paint--tide" role="img" aria-label="Abstract painting with raw beige canvas above dripping turquoise blue"></div>
      <figcaption class="artwork__title">In enim justo</figcaption>
    </figure>

    <figure class="artwork artwork--3">
      <div class="artwork__image paint--burst" role="img" aria-label="Abstract painting with teal, rust orange and black strokes bursting outward"></div>
      <figcaption class="artwork__title">Integer tincidunt</figcaption>
    </figure>

    <figure class="artwork artwork--4">
      <div class="artwork__image paint--sunwheel" role="img" aria-label="Abstract painting with swirling ochre yellow, brick red and blue strokes"></div>
      <figcaption class="artwork__title">Cras dapibus</figcaption>
    </figure>
  </main>

  <footer class="site-footer">©2022 Lena Marlowe Art. All rights reserved.</footer>
</body>
</html>
```